Bramblewood Card Company Business Cards

We are a trading card store with Glimmorax, sports and other TCG cards, we need a business card design that encompasses a clean cut, modern style with a retro flare. website is bramblewoodcardco.com for reference. Can utilize a comic book era feel or a more modern outdoor feel to utilize the "Pacific Northwest" elements of tress, mountains, etc.

Industry/Entity Type

Trading cards and collectibles

Contact Information for Business Card

business name, email address, phone number, name, owner job title

Font styles to use
Sans Serif

```html
<!DOCTYPE html>
<html lang="en">
<head>
<meta charset="utf-8">
<title>Bramblewood Card Company – Business Cards</title>
<link href="https://fonts.googleapis.com/css2?family=Montserrat:wght@400;600;700&display=swap" rel="stylesheet">
<style>
  :root {
    --backdrop: #9b9b9b;
    --card-light: #ffffff;
    --card-dark: #000000;
    --accent: #18bde2;
    --ink: #1a1a1a;
    --mark-grey: #6f6f6f;
    --mark-grey-dark: #7a7a7a;
  }
  * { margin: 0; padding: 0; box-sizing: border-box; }
  html, body {
    width: 1093px;
    height: 1200px;
    overflow: hidden;
    background: var(--backdrop);
    font-family: "Montserrat", sans-serif;
    color: var(--ink);
  }
  .canvas { position: relative; width: 1093px; height: 1200px; }
  .card {
    position: absolute;
    left: 264px;
    width: 597px;
    height: 364px;
    border-radius: 18px;
  }
  .card--front { top: 225px; background: var(--card-light); }
  .card--back { top: 616px; background: var(--card-dark); }

  .wordmark {
    position: absolute;
    display: flex;
    flex-direction: column;
    align-items: center;
    justify-content: center;
    text-align: center;
    font-weight: 700;
    text-transform: uppercase;
    line-height: 1.15;
  }
  .wordmark__dot { border-radius: 50%; background: var(--mark-grey); margin-bottom: 10px; }
  .card--front .wordmark {
    left: 88px; top: 126px; width: 166px; height: 152px;
    color: var(--mark-grey); font-size: 19px; letter-spacing: 0.5px;
  }
  .card--front .wordmark__dot { width: 14px; height: 14px; }
  .card--back .wordmark {
    left: 150px; top: 58px; width: 297px; height: 244px;
    color: var(--mark-grey-dark); font-size: 33px; letter-spacing: 1px;
  }
  .card--back .wordmark__dot { width: 22px; height: 22px; background: var(--mark-grey-dark); margin-bottom: 16px; }

  .divider {
    position: absolute; left: 270px; top: 125px;
    width: 2px; height: 150px; background: var(--accent);
  }
  .contact { position: absolute; left: 282px; top: 122px; }
  .contact__name {
    color: var(--accent); font-weight: 600; font-size: 24px; line-height: 1.1;
  }
  .contact__role { font-size: 13.5px; margin-top: 1px; margin-left: 1px; }
  .contact__address { font-size: 14px; line-height: 16px; margin-top: 11px; }
  .contact__list { list-style: none; margin-top: 8px; }
  .contact__item {
    display: flex; align-items: center; font-size: 14px; height: 20px;
  }
  .contact__item + .contact__item { margin-top: 4px; }
  .contact__item:first-child { margin-bottom: 2px; }
  .contact__icon { width: 14px; height: 14px; margin-right: 9px; flex: none; }
  .contact__item--mail .contact__icon,
  .contact__item--web .contact__icon { margin-right: 10px; }
</style>
</head>
<body>
<main class="canvas">
  <section class="card card--front">
    <div class="wordmark">
      <span class="wordmark__dot"></span>
      <span>Bramblewood</span>
      <span>Card Company</span>
    </div>
    <span class="divider"></span>
    <div class="contact">
      <h1 class="contact__name">Darian Holt</h1>
      <p class="contact__role">Owner</p>
      <p class="contact__address">2840 Cedar Ridge Blvd Suite<br>210 Tacoma, Washington 98402</p>
      <ul class="contact__list">
        <li class="contact__item contact__item--phone">
          <svg class="contact__icon" viewBox="0 0 24 24" aria-hidden="true"><path fill="var(--accent)" d="M6.6 10.8a15.1 15.1 0 0 0 6.6 6.6l2.2-2.2c.3-.3.7-.4 1-.2 1.1.4 2.3.6 3.6.6.6 0 1 .4 1 1V20c0 .6-.4 1-1 1A17 17 0 0 1 3 4c0-.6.4-1 1-1h3.5c.6 0 1 .4 1 1 0 1.3.2 2.5.6 3.6.1.3 0 .7-.2 1z"/></svg>
          06-48213957
        </li>
        <li class="contact__item contact__item--mail">
          <svg class="contact__icon" viewBox="0 0 24 24" aria-hidden="true"><rect x="2" y="5" width="20" height="14" fill="var(--accent)"/><path d="M2 5l10 8 10-8" fill="none" stroke="#fff" stroke-width="1.6"/></svg>
          info@bramblewoodcardcompany.com
        </li>
        <li class="contact__item contact__item--web">
          <svg class="contact__icon" viewBox="0 0 24 24" aria-hidden="true"><circle cx="12" cy="12" r="10" fill="var(--accent)"/><path d="M2 12h20M12 2c3 3 3 17 0 20M12 2c-3 3-3 17 0 20" fill="none" stroke="#fff" stroke-width="1.3"/></svg>
          www.bramblewoodcardcompany.com
        </li>
      </ul>
    </div>
  </section>

  <section class="card card--back">
    <div class="wordmark">
      <span class="wordmark__dot"></span>
      <span>Bramblewood</span>
      <span>Card Company</span>
    </div>
  </section>
</main>
</body>
</html>
```